Varnik Holdings — Business Card Design Brief
Overview
Design a double-sided business card for Varnik Holdings that highlights our two service arms: Varnik Communications (telecommunications) and Varnik Energy (business energy solutions). The card should feel smart and stand out when handed to clients.

Objectives
Showcase our areas of specialty clearly.
Reflect the overall Varnik / Varnik Holdings brand while acknowledging both arms.
Explore using both logos (Communications + Energy) or one unified logo, depending on the design.

Deliverables
One double-sided business card design (front + back).

Content & Copy
Front (preferred): Logo: Varnik / Varnik Holdings
Descriptor: Business Communications | Business Energy
Back:My contact details and company details
Core products: Business Mobile • Telephony • Internet • Business Energy Solutions

Brand & Visual Direction
We have a group logo currently tailored more toward telecoms, plus a separate Varnik Energy logo.
Please explore layouts that use both logos or just one, whichever works best.
Color: I wouldn't mind seeing an option using our the Blue/Purple gradient from our website (varnik-example.co.uk), but also open to non-gradient approaches and other colours..

Overall look: Smart, modern, and distinctive.
Format & Print Specs
Double-sided business card format. (Use a standard size

Must-Haves
Front: Varnik wording or Varnik Holdings wording with atleast 1 logo also on front “Business Communications | Business Energy.”

Back: Contact + company details and core products.
A design that stands out while remaining professional.

Nice-to-Have Options
A gradient version using our site’s Blue/Purple gradient.
A non-gradient version.
A dual-logo treatment versus a single-logo treatment.

Thanks
Owen

```html
<!DOCTYPE html>
<html lang="en">
<head>
<meta charset="utf-8">
<title>Varnik Holdings – Business Card</title>
<link href="https://fonts.googleapis.com/css2?family=Montserrat:wght@400;500;700&family=Poppins:wght@600;700&display=swap" rel="stylesheet">
<style>
  :root{
    --backdrop:#999999;
    --card:#ffffff;
    --navy:#1e1466;
    --green:#45a80c;
    --lime:#c8d60a;
    --ink:#1c1c1c;
    --charcoal:#333333;
    --blue:#1565d8;
  }
  *{margin:0;padding:0;box-sizing:border-box}
  html,body{width:1200px;height:1059px;overflow:hidden;background:var(--backdrop)}
  .card{position:absolute;left:253px;background:var(--card);border-radius:24px;overflow:hidden}
  .card-front{top:88px;width:723px;height:415px}
  .card-back{top:567px;width:712px;height:406px}

  .brand{position:absolute;display:flex;flex-direction:column;align-items:flex-start}
  .brand-mark{border-radius:50%}
  .brand-name{font-family:"Poppins",sans-serif;font-weight:700;color:var(--navy);letter-spacing:-1px;line-height:1}
  .front-brand{left:47px;top:29px}
  .front-brand .brand-mark{width:108px;height:108px;border:14px solid var(--green)}
  .front-brand .brand-name{font-size:54px;margin-top:6px}

  .person{position:absolute;right:39px;top:46px;text-align:right;font-family:"Montserrat",sans-serif}
  .person-name{font-weight:700;font-size:29px;color:var(--navy);line-height:1.1}
  .person-role{font-weight:400;font-size:19px;color:var(--ink);margin-top:2px;padding-right:5px}
  .accent-bar{position:absolute;right:0;top:50px;width:11px;height:51px;background:var(--navy)}

  .contact{position:absolute;left:46px;top:222px;list-style:none;font-family:"Montserrat",sans-serif;font-size:20px;color:var(--ink)}
  .contact li{display:flex;align-items:flex-start;height:34px}
  .contact .icon{width:20px;height:20px;margin-right:9px;margin-top:3px;fill:var(--green);flex:none}
  .contact .addr{line-height:33px}

  .services{position:absolute;right:39px;top:286px;text-align:right;font-family:"Montserrat",sans-serif;font-weight:700;font-size:20px;color:var(--navy);line-height:28px}

  .footer-band{position:absolute;left:0;bottom:0;width:100%;height:12px}

  .back-title{position:absolute;left:0;right:0;top:64px;text-align:center;font-family:"Poppins",sans-serif;font-weight:600;font-size:53px;color:var(--charcoal);line-height:1}
  .back-brand{left:50%;top:158px;transform:translateX(-50%);align-items:center}
  .back-brand .brand-mark{width:112px;height:112px;border:14px solid var(--blue)}
  .back-brand .brand-name{font-size:56px;margin-top:10px}
</style>
</head>
<body>

<section class="card card-front">
  <div class="brand front-brand">
    <span class="brand-mark"></span>
    <span class="brand-name">VARNIK</span>
  </div>

  <div class="person">
    <div class="person-name">Marcus Hale</div>
    <div class="person-role">Owner</div>
  </div>
  <span class="accent-bar"></span>

  <ul class="contact">
    <li><svg class="icon" viewBox="0 0 24 24"><path d="M6.6 10.8a15 15 0 0 0 6.6 6.6l2.2-2.2c.3-.3.7-.4 1-.2 1.1.4 2.3.6 3.6.6.6 0 1 .4 1 1V20c0 .6-.4 1-1 1A17 17 0 0 1 3 4c0-.6.4-1 1-1h3.5c.6 0 1 .4 1 1 0 1.3.2 2.5.6 3.6.1.3 0 .7-.2 1z"/></svg><span>044-987 654 321</span></li>
    <li><svg class="icon" viewBox="0 0 24 24"><path d="M2 5h20v14H2z M2 5l10 7 10-7" /><path d="M3 6l9 6.3L21 6v1.6l-9 6.3-9-6.3z" fill="#fff"/></svg><span>info@varnik-example.co.uk</span></li>
    <li><svg class="icon" viewBox="0 0 24 24"><circle cx="12" cy="12" r="10"/><path d="M8 5c2 1 1 3 3 4s1 3-1 3-3 2-2 4M15 4c-1 2 1 3 2 4s3 1 4 1M14 14c2 0 3 1 3 3s-1 3-2 4" stroke="#fff" stroke-width="1.6" fill="none"/></svg><span>www.varnik-example.co.uk</span></li>
    <li><svg class="icon" viewBox="0 0 24 24"><path d="M12 2a7 7 0 0 0-7 7c0 5 7 13 7 13s7-8 7-13a7 7 0 0 0-7-7zm0 9.5A2.5 2.5 0 1 1 12 6.5a2.5 2.5 0 0 1 0 5z"/></svg><span class="addr">18 Harbour Row, Suite 4<br>LN4 2QB, United Kingdom</span></li>
  </ul>

  <div class="services">
    • Business Mobile<br>
    • Telephony • Internet<br>
    • Business Energy Solutions
  </div>

  <svg class="footer-band" viewBox="0 0 723 12" preserveAspectRatio="none">
    <polygon points="0,0 354,0 359,12 0,12" fill="var(--navy)"/>
    <polygon points="360,0 723,0 723,12 365,12" fill="var(--green)"/>
  </svg>
</section>

<section class="card card-back">
  <h1 class="back-title">Varnik Holdings</h1>
  <div class="brand back-brand">
    <span class="brand-mark"></span>
    <span class="brand-name">VARNIK</span>
  </div>
</section>

</body>
</html>
```